VIP Card Design Project

uZorvo is a premium sneaker store selling brand name sneakers like Volta, Rexa, Kembro and etc. ( www.uzorvoshop.com ) We need to design a VIP card to promote one of our discount program called "Uzorvo VIP Band 17", which offers 24% discount off all full-priced items. The idea is because we have a "Peakline Gym center" (peaklinegym.com) next door and we are trying to design a discount program for people going to the fitness center.
The design is for the front of the card. The back will be black and white with benefits information and member information.
The front design need to include our logo, "VIP", "Band 17" and our web address "Uzorvo.com" and Chatterly and quibbr logo.
It will be a plastic card in the size of 3.375x2.125 (bleed size 3.5x2.25)

```html
<!DOCTYPE html>
<html lang="en">
<head>
<meta charset="utf-8">
<title>Uzorvo VIP Band 17 Card</title>
<link rel="stylesheet" href="https://fonts.googleapis.com/css2?family=PT+Sans:wght@400;700&family=VT323&display=swap">
<style>
  :root {
    --bg: #ece7e1;
    --card: #ffffff;
    --green: #3dae3f;
    --green-dark: #1f6b22;
    --green-band: #2a7a2c;
    --text-green: #2f7d2f;
    --orange: #f0891e;
    --navy: #1f3a78;
    --ink: #1a1a1a;
    --shoe: #9aa39b;
  }
  html, body {
    margin: 0;
    width: 1065px;
    height: 1200px;
    overflow: hidden;
    background: var(--bg);
    font-family: "PT Sans", sans-serif;
  }
  .stage { position: relative; width: 1065px; height: 1200px; }
  .card {
    position: absolute;
    left: 122px;
    width: 825px;
    height: 517px;
    background: var(--card);
    border-radius: 30px;
    box-shadow: 0 6px 18px rgba(0,0,0,.18);
    overflow: hidden;
  }
  .card--front { top: 51px; }
  .card--back { top: 629px; }

  .brand {
    position: absolute;
    top: 62px; left: 0; right: 0;
    text-align: center;
    font-weight: 700;
    font-size: 140px;
    line-height: 1;
    color: var(--green);
    letter-spacing: 2px;
  }
  .band {
    position: absolute;
    left: 0; right: 0;
    background: linear-gradient(90deg, var(--green-dark), var(--green-band) 20%, #3b9a3c 50%, var(--green-band) 80%, var(--green-dark));
    border-top: 3px solid var(--navy);
    box-shadow: 0 -7px 0 -4px var(--navy);
    color: #fff;
    font-weight: 700;
    text-align: center;
  }
  .band--title { top: 228px; height: 51px; font-size: 44px; line-height: 51px; }
  .band--benefits { top: 50px; height: 46px; font-size: 36px; line-height: 46px; }
  .flourish {
    position: absolute;
    top: 50%;
    width: 135px; height: 26px;
    margin-top: -13px;
    border-radius: 13px;
    background: rgba(200, 230, 120, .35);
  }
  .flourish--left { left: 35px; }
  .flourish--right { right: 35px; }

  .shoe {
    position: absolute;
    top: 307px;
    width: 147px; height: 106px;
    border: 3px solid var(--green);
    border-radius: 28px;
    box-sizing: border-box;
  }
  .shoe--one { left: 107px; background: linear-gradient(160deg, #8f8a84, #d9d5d0 55%, #5a5652); }
  .shoe--two { left: 352px; background: linear-gradient(160deg, #6d6459, #e9e6e0 55%, #7b6f61); }
  .shoe--three { left: 577px; background: linear-gradient(160deg, #f4f4f2, #e2c21a 50%, #1c1c1c); }

  .offer {
    position: absolute;
    top: 414px; left: 0; right: 0;
    text-align: center;
    font-family: "VT323", monospace;
    font-size: 38px;
    color: var(--ink);
  }
  .web {
    position: absolute;
    top: 453px; left: 0; right: 0;
    text-align: center;
    font-size: 25px;
    color: var(--ink);
  }
  .social {
    position: absolute;
    top: 458px;
    display: flex;
    align-items: center;
    gap: 6px;
    font-size: 16px;
    color: var(--navy);
  }
  .social--chatterly { left: 185px; }
  .social--quibbr { right: 95px; }
  .social__dot { width: 16px; height: 16px; border-radius: 3px; background: var(--navy); }

  .intro {
    position: absolute;
    top: 104px; left: 40px;
    font-size: 19px;
    font-weight: 700;
    color: var(--orange);
  }
  .benefits {
    position: absolute;
    top: 145px; left: 40px; right: 40px;
    margin: 0; padding: 0;
    list-style: none;
    font-size: 18.5px;
    line-height: 25px;
    color: var(--text-green);
  }
  .benefits li { display: flex; margin-bottom: 14px; }
  .benefits__mark { width: 34px; flex: none; }
  .member {
    position: absolute;
    top: 467px; left: 42px; right: 40px;
    display: flex;
    font-size: 19px;
    font-weight: 700;
  }
  .member__name { color: var(--green-dark); display: flex; align-items: flex-end; }
  .member__id { color: var(--orange); display: flex; align-items: flex-end; margin-left: 20px; }
  .member__line { display: inline-block; border-bottom: 2px solid var(--navy); margin-left: 4px; margin-bottom: 4px; }
  .member__name .member__line { width: 300px; }
  .member__id .member__line { width: 160px; }
</style>
</head>
<body>
<div class="stage">
  <section class="card card--front">
    <div class="brand">uZorvo</div>
    <div class="band band--title">
      <span class="flourish flourish--left" role="img" aria-label="Decorative green swirl"></span>
      Uzorvo VIP Band 17
      <span class="flourish flourish--right" role="img" aria-label="Decorative green swirl"></span>
    </div>
    <div class="shoe shoe--one" role="img" aria-label="Photo of a white and red running sneaker"></div>
    <div class="shoe shoe--two" role="img" aria-label="Photo of a white sneaker with dark green stripes"></div>
    <div class="shoe shoe--three" role="img" aria-label="Photo of a black and yellow sneaker"></div>
    <div class="offer">24% Discount of All Full Priced Items</div>
    <div class="web">www.uzorvoshop.com</div>
    <div class="social social--chatterly"><span class="social__dot"></span>Chatterly</div>
    <div class="social social--quibbr"><span class="social__dot"></span>quibbr</div>
  </section>

  <section class="card card--back">
    <div class="band band--benefits">
      <span class="flourish flourish--left" role="img" aria-label="Decorative green swirl"></span>
      uZorvo Benefits
      <span class="flourish flourish--right" role="img" aria-label="Decorative green swirl"></span>
    </div>
    <div class="intro">The UZORVO Member Program entitles Members to the following benefits:</div>
    <ol class="benefits">
      <li><span class="benefits__mark">a.</span><span>20% OFF your entire first purchase after you sign up (Limited Time Offer).<br>Certain items are excluded from this offer. Please see stores for details.</span></li>
      <li><span class="benefits__mark">b.</span><span>10% OFF every purchase while being a member.<br>Certain items are excluded from this offer. Please see stores for details.</span></li>
      <li><span class="benefits__mark">c.</span><span>Additional 10% OFF and FREE SHIPPING when an item is out of stock<br>in store but can be shipped to you from another location.</span></li>
      <li><span class="benefits__mark">d.</span><span>Eligible to purchase exclusive items offered to members only.<br>Purchasing of exclusive items is limited to 1 item per member per 30 days.<br>Please see stores for details.</span></li>
    </ol>
    <div class="member">
      <div class="member__name">Member Name :<span class="member__line"></span></div>
      <div class="member__id">Member ID :<span class="member__line"></span></div>
    </div>
  </section>
</div>
</body>
</html>
```